Bramwell IT Services Business Card

Bramwell IT Services are a Perth based IT Services company. We would like to incorporate our company logo (attached) and stick with the blue that is in that design. I would like a clean look design that isn't too busy, yet creates a lasting image that is instantly recognisable in the recipients mind.

Target Market(s)

The target audience is small/medium business owners.

Industry/Entity Type

Business

Font styles to use
Serif
Sans Serif

Colors

Designer to choose colors to be used in the design.

Requirements
Must have
• The design should include:
Business name: Bramwell IT Services
Directors Name: Marcus Tenley
Phone Number: 0483 562 904
Email: support@bramwellit.com.au
Website: www.bramwellit.com.au

```html
<!DOCTYPE html>
<html lang="en">
<head>
<meta charset="utf-8">
<title>Bramwell IT Services – Business Card</title>
<link rel="stylesheet" href="https://fonts.googleapis.com/css2?family=Lato:wght@400;700;900&display=swap">
<style>
  :root {
    --backdrop: #2b2b2d;
    --card: #ffffff;
    --card-shade: #e9ebee;
    --brand-blue: #3ab4ea;
    --brand-blue-deep: #1f9ad6;
    --navy: #1d3f8f;
    --ink: #1a1a1a;
    --muted: #9a9a9a;
  }
  * { box-sizing: border-box; margin: 0; padding: 0; }
  html, body { width: 1200px; height: 900px; overflow: hidden; }
  body {
    background: var(--backdrop);
    font-family: "Lato", Arial, sans-serif;
    display: flex;
    flex-direction: column;
    align-items: center;
    justify-content: center;
    gap: 60px;
  }
  .card {
    position: relative;
    width: 630px;
    height: 360px;
    border-radius: 18px;
    overflow: hidden;
    background: linear-gradient(180deg, var(--card) 40%, var(--card-shade) 100%);
  }
  .brand {
    display: flex;
    align-items: center;
    gap: 14px;
  }
  .brand-dot {
    width: 46px;
    height: 46px;
    border-radius: 50%;
    background: var(--brand-blue);
  }
  .brand-name {
    font-weight: 900;
    color: var(--navy);
    font-size: 30px;
    letter-spacing: 0.5px;
  }

  /* Front */
  .card-front .brand { position: absolute; left: 70px; top: 105px; }
  .card-front .tagline {
    position: absolute;
    left: 70px; right: 40px; top: 190px;
    color: var(--muted);
    font-size: 17px;
  }
  .card-front .band {
    position: absolute;
    left: 0; right: 0; bottom: 0;
    height: 62px;
    background: var(--brand-blue);
  }

  /* Back */
  .card-back .band {
    position: absolute;
    left: 0; right: 0; top: 0;
    height: 58px;
    background: var(--brand-blue);
    color: #fff;
    text-align: right;
    padding: 8px 28px 0 0;
  }
  .director-name { font-weight: 700; font-size: 19px; line-height: 1.15; }
  .director-role { font-size: 14px; }
  .contact {
    position: absolute;
    right: 28px; top: 84px;
    text-align: right;
    font-size: 15px;
    line-height: 1.6;
    color: var(--ink);
  }
  .contact .label { color: var(--brand-blue-deep); font-weight: 700; }
  .card-back .brand { position: absolute; left: 40px; top: 190px; }
  .company {
    position: absolute;
    right: 28px; bottom: 38px;
    text-align: right;
  }
  .company-name { font-weight: 900; font-size: 18px; color: var(--ink); }
  .company-note { font-weight: 700; font-size: 15px; color: var(--brand-blue-deep); }
</style>
</head>
<body>
  <section class="card card-front">
    <div class="brand">
      <span class="brand-dot"></span>
      <span class="brand-name">Bramwell IT Services</span>
    </div>
    <p class="tagline">Network solution to help you efficiently manage your business.</p>
    <div class="band"></div>
  </section>

  <section class="card card-back">
    <header class="band">
      <div class="director-name">Marcus Tenley</div>
      <div class="director-role">Designation</div>
    </header>
    <div class="contact">
      <div><span class="label">Telephone:</span> 0483 562 904</div>
      <div><span class="label">Email:</span> support@bramwellit.com.au</div>
      <div><span class="label">Web:</span> www.bramwellit.com.au</div>
    </div>
    <div class="brand">
      <span class="brand-dot"></span>
      <span class="brand-name">Bramwell IT Services</span>
    </div>
    <div class="company">
      <div class="company-name">BRAMWELL IT SERVICES</div>
      <div class="company-note">12 years experience in the IT industry</div>
    </div>
  </section>
</body>
</html>
```